Calm Harbor Bodywork business is seeking a Business Card Design

We are a new natural therapy business that needs a Business Card Design with an appointment card on the back.

We offer Myotherapy (muscle therapy) services and have a strong focus and commitment to helping people relieve pain and restore movement to their bodies.

I am attaching my business logo for you information.

Business card must contain my logo and have space for name, title, qualifications, phone number, email, web address

Appointment Card on the back of the card must contain space to write next appointment date, time and name of therapist and cancellation policy.

Cancellation Policy
Minimum of 24hrs notice is required prior to appointment time or full treatment fees with apply.

```html
<!DOCTYPE html>
<html lang="en">
<head>
<meta charset="utf-8">
<title>Calm Harbor Bodywork – Business Card and Appointment Card</title>
<link href="https://fonts.googleapis.com/css2?family=Lato:wght@400;700;900&display=swap" rel="stylesheet">
<style>
  :root {
    --backdrop: #e6e6e6;
    --card: #ffffff;
    --brand-red: #c41e35;
    --ink: #1a1a1a;
    --rule: #555555;
    --divider-fade: rgba(196, 30, 53, 0);
  }
  * { box-sizing: border-box; margin: 0; padding: 0; }
  html, body {
    width: 1200px; height: 900px; overflow: hidden;
    background: var(--backdrop);
    font-family: "Lato", Arial, sans-serif;
  }
  .card {
    position: absolute; left: 250px;
    width: 700px; height: 400px;
    background: var(--card);
    box-shadow: 0 10px 24px rgba(0,0,0,0.16);
  }
  .appointment-card { top: 30px; }
  .business-card { top: 470px; }

  /* shared brand lockup */
  .brand-lockup { position: absolute; display: flex; align-items: center; gap: 13px; }
  .brand-square { width: 46px; height: 46px; background: var(--brand-red); flex: none; }
  .brand-name {
    font-weight: 700; font-size: 24px; line-height: 1.15;
    color: var(--brand-red); letter-spacing: 0.3px;
  }

  /* appointment card (back) */
  .appointment-fields { position: absolute; left: 36px; top: 40px; width: 390px; }
  .label-band {
    display: inline-block; background: var(--brand-red); color: #fff;
    font-weight: 900; font-size: 15px; letter-spacing: 0.5px;
    padding: 5px 10px;
  }
  .field-row {
    display: flex; align-items: flex-end; gap: 8px;
    margin-top: 26px; font-weight: 700; font-size: 15px; color: var(--ink);
  }
  .field-row:first-of-type { margin-top: 30px; }
  .field-line { flex: 1; border-bottom: 2px dotted var(--rule); height: 4px; margin-bottom: 4px; }
  .field-gap { width: 14px; flex: none; }
  .policy { margin-top: 36px; }
  .policy-text {
    margin-top: 12px; font-weight: 700; font-size: 16px;
    line-height: 1.4; color: var(--ink);
  }
  .appointment-card .brand-lockup { left: 460px; top: 175px; }

  /* business card (front) */
  .business-card .brand-lockup { left: 46px; top: 120px; }
  .mission {
    position: absolute; left: 20px; width: 320px; bottom: 48px;
    text-align: center; color: var(--brand-red);
    font-weight: 900; font-size: 18px; line-height: 1.3;
  }
  .divider {
    position: absolute; left: 357px; top: 30px; width: 3px; height: 330px;
    background: linear-gradient(to bottom, var(--divider-fade), var(--brand-red) 70%);
  }
  .contact-panel { position: absolute; left: 385px; top: 44px; right: 16px; }
  .holder-name { color: var(--brand-red); font-weight: 900; font-size: 22px; line-height: 1.1; }
  .holder-title { color: var(--ink); font-weight: 700; font-size: 13px; letter-spacing: 0.4px; }
  .address {
    margin-top: 70px; color: var(--brand-red);
    font-weight: 900; font-size: 16px; line-height: 1.3;
  }
  .contact-row {
    display: flex; align-items: center; gap: 12px;
    margin-top: 12px; color: var(--ink); font-size: 15.5px;
  }
  .contact-icon { width: 18px; height: 15px; flex: none; }
  .website { margin-top: 16px; color: var(--brand-red); font-weight: 900; font-size: 16px; }
</style>
</head>
<body>
  <section class="card appointment-card">
    <div class="appointment-fields">
      <span class="label-band">NEXT APPOINTMENT</span>
      <div class="field-row">
        <span>DATE:</span><span class="field-line"></span>
        <span class="field-gap"></span>
        <span>TIME:</span><span class="field-line"></span>
      </div>
      <div class="field-row">
        <span>THERAPIST:</span><span class="field-line"></span>
      </div>
      <div class="policy">
        <span class="label-band">CANCELLATION POLICY</span>
        <p class="policy-text">Minimum of 24hrs notice is required prior to appointment time or full treatment fees with apply</p>
      </div>
    </div>
    <div class="brand-lockup">
      <span class="brand-square"></span>
      <span class="brand-name">Calm Harbor<br>Bodywork</span>
    </div>
  </section>

  <section class="card business-card">
    <div class="brand-lockup">
      <span class="brand-square"></span>
      <span class="brand-name">Calm Harbor<br>Bodywork</span>
    </div>
    <p class="mission">Assists you to overcome<br>Acute &amp; Chronic pain &amp; injury<br>through Calm Harbor Bodywork</p>

    <div class="divider"></div>

    <div class="contact-panel">
      <h1 class="holder-name">YOUR NAME</h1>
      <p class="holder-title">DESIGNATION</p>
      <p class="address">Level 2 / 118 Harbour Lane,<br>Easton, VIC 3190</p>
      <div class="contact-row">
        <svg class="contact-icon" viewBox="0 0 26 22" aria-hidden="true">
          <path d="M2 7 Q13 0 24 7 L22 10 L18 9 L18 6 Q13 4 8 6 L8 9 L4 10 Z" fill="var(--brand-red)"/>
          <path d="M6 11 L20 11 L23 20 L3 20 Z" fill="var(--brand-red)"/>
          <circle cx="13" cy="15.5" r="2.5" fill="#fff"/>
        </svg>
        <span>+61 400 555 018</span>
      </div>
      <div class="contact-row">
        <svg class="contact-icon" viewBox="0 0 26 22" aria-hidden="true">
          <rect x="1" y="3" width="24" height="16" fill="var(--brand-red)"/>
          <path d="M1 3 L13 12 L25 3" fill="none" stroke="#fff" stroke-width="2"/>
        </svg>
        <span>Info@calmharborbodywork.com.au</span>
      </div>
      <p class="website">www.calmharborbodywork.com.au</p>
    </div>
  </section>
</body>
</html>
```